Web application layout remake

We are looking for a makeover on our web application called “KRVcrate” - it's a document management and digital archiving system integrating workflows and allowing you to free up physical space in your office currently occupied with documents by moving them to secure external custody.
We are expecting you to include the following:
• homepage
• signup page
• application page
This project is for the whole website (which is not big at all anyway!) and not just for the design of one page. The coding should be in HTML5 only.
We are aiming for fresh, appealing, clean, user friendly ,web 2.0, jquery layout.
Remakes or changes on the logo are welcome.
The application will be sold through the portal.
Please find in attachment the print screen of the application to aid you (this is the current view customers have after logging in but the layout is obsolete and we want a brand new!).
Reason: Still not happy with the received layouts. Keep up the good work! Thanks!
Reason: Still not happy with the whole solution and finding alternate app interfaces!

```html
<!DOCTYPE html>
<html lang="en">
<head>
<meta charset="utf-8">
<title>KRVcrate — Document Management</title>
<link href="https://fonts.googleapis.com/css2?family=Roboto+Condensed:wght@300;400&display=swap" rel="stylesheet">
<style>
:root{
  --top-strip:#1b62bd;
  --navy:#00306a;
  --panel:#0f58b0;
  --panel-line:#0a4690;
  --field:#e4e4e4;
  --field-text:#8a8a8a;
  --btn-blue:#0a4ea6;
  --white:#ffffff;
  --bronze:#4a1675;
  --silver:#e8461c;
  --gold:#d9a70c;
  --platinum:#f07a55;
  --card-border:#d6d6d6;
  --card-foot:#f2f2f2;
  --dark-btn:#3c3c3c;
  --text:#333333;
  --accent:#e8501c;
  --footer:#f0f0f0;
  --footer-text:#555555;
}
*{margin:0;padding:0;box-sizing:border-box}
html,body{width:1200px;height:1115px;overflow:hidden}
body{position:relative;background:var(--white);font-family:"Roboto Condensed",Arial,sans-serif;color:var(--text)}
.hero{position:absolute;left:0;top:0;width:1200px;height:670px;background:var(--navy);border-top:12px solid var(--top-strip)}
.brand{position:absolute;left:122px;top:43px;display:flex;align-items:center;gap:10px;color:var(--white);font-size:35px;font-weight:300;line-height:40px}
.brand-mark{width:42px;height:42px;border-radius:50%;background:var(--white)}
.nav{list-style:none;font-size:17px;color:var(--white)}
.nav li{position:absolute;top:53px;line-height:20px;white-space:nowrap}
.nav .new{left:544px}
.nav .pricing{left:688px}
.nav .trial{left:809px;letter-spacing:.3px}
.nav .login{left:983px;top:45px;width:94px;height:36px;line-height:36px;text-align:center;background:#1260c0;border-radius:18px}
.header-rule{position:absolute;left:200px;top:116px;width:800px;height:2px;background:linear-gradient(90deg,transparent,#00224d,transparent)}
.hero-photo{position:absolute;left:140px;top:140px;width:370px;height:518px;border-radius:180px 180px 0 0;background:radial-gradient(ellipse at 45% 35%,#b98a6a 0%,#6d88b8 45%,#0a3a78 80%,transparent 100%)}
.register{position:absolute;left:650px;top:165px;width:380px;height:458px;background:var(--panel);border-radius:20px;text-align:center;color:var(--white)}
.register h2{font-weight:400;font-size:23px;height:67px;line-height:70px;border-bottom:1px solid var(--panel-line)}
.field{display:block;width:342px;height:42px;margin:29px auto 0;border-radius:21px;background:linear-gradient(#f2f2f2,var(--field));border:1px solid #c9c9c9;box-shadow:inset 0 2px 3px rgba(0,0,0,.25);padding-left:16px;text-align:left;line-height:42px;font-size:13px;font-weight:300;color:var(--field-text)}
.field + .field{margin-top:19px}
.register-btn{display:inline-block;margin-top:19px;width:172px;height:43px;line-height:42px;border-radius:22px;background:linear-gradient(#2a78d4,var(--btn-blue));border:1px solid #063d85;font-size:16px}
.terms{margin-top:20px;font-size:13px;line-height:17px;font-weight:300}
.plans{position:absolute;top:688px;left:120px;display:flex;gap:24px}
.plan{width:222px;height:198px;border:1px solid var(--card-border);background:var(--white);text-align:center}
.plan-head{margin:6px 5px 0;height:65px;display:flex;align-items:center;color:var(--white)}
.plan-name{flex:1;text-align:left;padding-left:10px;font-size:24px;font-weight:300}
.plan-price{width:86px;border-left:1px solid rgba(0,0,0,.3);font-size:38px;font-weight:300;height:52px;line-height:52px}
.bronze{background:linear-gradient(90deg,#5b1f8a,var(--bronze))}
.silver{background:linear-gradient(#f05a22,var(--silver))}
.gold{background:linear-gradient(#e8b614,var(--gold))}
.platinum{background:linear-gradient(#f38a62,var(--platinum))}
.plan ul{list-style:none;font-size:17px;font-weight:300;color:#555}
.plan li{height:30px;line-height:30px}
.plan li:first-child{margin-top:6px;border-bottom:1px solid #e2e2e2}
.plan-foot{margin-top:6px;background:var(--card-foot);height:54px;padding-top:9px}
.buy{display:inline-block;width:110px;height:38px;line-height:38px;border-radius:19px;background:linear-gradient(#555,var(--dark-btn));color:var(--white);font-size:15px;font-weight:300}
.intro{position:absolute;top:922px;left:0;width:1200px;text-align:center;text-transform:uppercase}
.intro h3{color:var(--accent);font-weight:300;font-size:23px;line-height:28px}
.intro p{margin-top:4px;font-size:13px;line-height:30px;color:#222;width:930px;margin-left:auto;margin-right:auto}
.footer{position:absolute;top:1040px;left:0;width:1200px;height:75px;background:var(--footer);border-top:2px solid #e0e0e0;color:var(--footer-text);font-size:11px;font-weight:300;text-transform:uppercase}
.footer-links{position:absolute;left:120px;top:16px;display:flex;gap:9px;list-style:none}
.copyright{position:absolute;left:117px;top:46px}
.social{position:absolute;left:953px;top:25px}
</style>
</head>
<body>
<header class="hero">
  <div class="brand"><span class="brand-mark"></span>KRVcrate</div>
  <ul class="nav">
    <li class="new">NEW STUFF</li>
    <li class="pricing">PRICING</li>
    <li class="trial">60-DAY FREE TRIAL</li>
    <li class="login">LOG IN</li>
  </ul>
  <div class="header-rule"></div>
  <div class="hero-photo" role="img" aria-label="Photo of a smiling businesswoman in a striped blue shirt"></div>
  <form class="register">
    <h2>REGISTER NOW!</h2>
    <div class="field">Your full Name:</div>
    <div class="field">Company:</div>
    <div class="field">Email:</div>
    <div class="field">Password:</div>
    <div class="register-btn">REGISTER NOW!</div>
    <p class="terms">By clicking you agree to the Terms of Service,<br>Privacy, and Refund policies.</p>
  </form>
</header>

<section class="plans">
  <div class="plan"><div class="plan-head bronze"><span class="plan-name">BRONZE</span><span class="plan-price">$39</span></div>
    <ul><li>›› 10 GB</li><li>›› 10 USERS</li></ul><div class="plan-foot"><span class="buy">BUY NOW!</span></div></div>
  <div class="plan"><div class="plan-head silver"><span class="plan-name">SILVER</span><span class="plan-price">$39</span></div>
    <ul><li>›› 25 GB</li><li>›› 25 USERS</li></ul><div class="plan-foot"><span class="buy">BUY NOW!</span></div></div>
  <div class="plan"><div class="plan-head gold"><span class="plan-name">GOLD</span><span class="plan-price">$39</span></div>
    <ul><li>›› 50 GB</li><li>›› 50 USERS</li></ul><div class="plan-foot"><span class="buy">BUY NOW!</span></div></div>
  <div class="plan"><div class="plan-head platinum"><span class="plan-name">PLATINUM</span><span class="plan-price">$39</span></div>
    <ul><li>›› 100 GB</li><li>›› 100 USERS</li></ul><div class="plan-foot"><span class="buy">BUY NOW!</span></div></div>
</section>

<section class="intro">
  <h3>Unde omnis iste natus error sit voluptatem accusantium doloremque laudantium,</h3>
  <p>Totam rem aperiam, eaque ipsa quae ab illo inventore veritatis et quasi architecto beatae vitae dicta sunt explicabo. Nemo enim ipsam voluptatem quia voluptas sit aspernatur aut odit aut fugit, sed quia consequuntur magn</p>
</section>

<footer class="footer">
  <ul class="footer-links">
    <li>Help</li><li>|</li><li>Mobile</li><li>Integrations</li><li>Security</li><li>Privacy</li><li>Terms</li><li>Contact</li>
  </ul>
  <p class="copyright">Copyright ©1999-2013 Quillmarsh, LLC. All rights reserved.</p>
  <svg class="social" width="120" height="28" viewBox="0 0 120 28" aria-label="Social links">
    <circle cx="13" cy="13" r="12.5" fill="#555"/>
    <circle cx="43" cy="13" r="12.5" fill="#555"/>
    <circle cx="73" cy="13" r="12.5" fill="#555"/>
    <circle cx="103" cy="13" r="12.5" fill="#555"/>
  </svg>
</footer>
</body>
</html>
```